New business card/stationary for a consulting company

I am looking for a clean and very professional looking business card for my consulting company as well as corresponding stationary. I am uploading our logo. I like simple and powerful for the feel. No graphics but I am open on everything else. Below is my contact information but would like the final to be in a version I can add my employees information into and print. Thank you.

Daniel Whitcombe
dan@ferncliffadvisory.com
2870 North 9th Avenue, Summit Floor, Elm Ridge, Illinois 60531
www.ferncliffadvisory.com

Industry/Entity Type

Consulting

Contact Information for Business Card

Daniel Whitcombe
dan@ferncliffadvisory.com
www.ferncliffadvisory.com

Font styles to use
Serif
Sans Serif

Requirements
Must have
• Our logo and the business card details.
Nice to have
• our website www.ferncliffadvisory.com

```html
<!DOCTYPE html>
<html lang="en">
<head>
<meta charset="utf-8">
<title>Ferncliff Advisory — Business Card</title>
<link href="https://fonts.googleapis.com/css2?family=Roboto:wght@300;400&display=swap" rel="stylesheet">
<style>
  :root {
    --backdrop: #3b3b3d;
    --card: #1f1f22;
    --card-edge: #2a2a2e;
    --brand-blue: #1d4f86;
    --ink-light: #f2f2f2;
    --ink-muted: #5a5a60;
  }
  * { margin: 0; padding: 0; box-sizing: border-box; }
  html, body {
    width: 799px; height: 1200px; overflow: hidden;
    background: var(--backdrop);
    font-family: "Roboto", Arial, sans-serif;
  }
  .stage {
    width: 799px; height: 1200px;
    display: flex; flex-direction: column;
    align-items: center; justify-content: space-around;
    padding: 70px 0;
  }
  .card {
    position: relative;
    width: 630px; height: 360px;
    background: var(--card);
    border: 1px solid var(--card-edge);
    box-shadow: 0 14px 30px rgba(0,0,0,0.45);
  }
  /* Front */
  .card--front .brand-mark {
    position: absolute; left: 50%; top: 50%;
    transform: translate(-50%, -50%);
    display: flex; align-items: center; gap: 16px;
  }
  .brand-mark__square {
    width: 34px; height: 34px; background: var(--ink-muted);
  }
  .brand-mark__name {
    font-weight: 300; font-size: 50px; letter-spacing: 2px;
    color: var(--ink-muted);
  }
  /* Back */
  .card--back .brand-block {
    position: absolute; left: 34px; top: 110px;
    display: flex; align-items: center; gap: 12px;
  }
  .brand-block__square {
    width: 30px; height: 30px; background: var(--brand-blue);
  }
  .brand-block__name {
    font-weight: 300; font-size: 36px; letter-spacing: 1px;
    color: var(--ink-light);
  }
  .contact {
    position: absolute; left: 300px; top: 168px;
    color: var(--ink-light); font-size: 16px; line-height: 24px;
  }
  .contact__name {
    color: var(--brand-blue); font-size: 20px; font-weight: 300;
    letter-spacing: 2px; text-transform: uppercase; margin-bottom: 4px;
  }
  .contact__row { display: flex; align-items: center; gap: 10px; }
  .contact__row svg { width: 12px; height: 12px; flex: none; }
  .contact__address { margin-top: 2px; }
</style>
</head>
<body>
<main class="stage">
  <section class="card card--front" aria-label="Card front">
    <div class="brand-mark">
      <span class="brand-mark__square"></span>
      <span class="brand-mark__name">Ferncliff</span>
    </div>
  </section>

  <section class="card card--back" aria-label="Card back">
    <div class="brand-block">
      <span class="brand-block__square"></span>
      <span class="brand-block__name">Ferncliff</span>
    </div>
    <div class="contact">
      <p class="contact__name">Daniel Whitcombe</p>
      <p class="contact__row">
        <svg viewBox="0 0 12 12" aria-hidden="true"><rect x="0.5" y="2" width="11" height="8" fill="#1d4f86"/><path d="M0.5 2 L6 6.5 L11.5 2" stroke="#1f1f22" fill="none"/></svg>
        dan@ferncliffadvisory.com
      </p>
      <p class="contact__row">
        <svg viewBox="0 0 12 12" aria-hidden="true"><circle cx="6" cy="6" r="5.5" fill="#1d4f86"/><path d="M0.5 6 H11.5 M6 0.5 C3 3 3 9 6 11.5 M6 0.5 C9 3 9 9 6 11.5" stroke="#1f1f22" fill="none" stroke-width="0.8"/></svg>
        www.ferncliffadvisory.com
      </p>
      <p class="contact__address">2870 North 9th Avenue, Summit<br>Floor, Elm Ridge, Illinois 60531</p>
    </div>
  </section>
</main>
</body>
</html>
```